Upmarket Dessert Lounge needs a Business Card Design

We are an upmarket dessert lounge needing a business card to match our image.

We want something that is simple yet beautiful, feminine, classy, sophisticated and elegant. We want it to stand out and don't mind if it is bold.

The design should include our logo and colours of red or maroon with gold highlights. We don't mind if black is used.

Marlow & Quince

Target Market(s)

For those who like to indulge or treat themselves and give in to their temptations on good quality desserts.

Industry/Entity Type

Business

Requirements
Must have
• Must include our logo and our name

Marlow & Quince

M & Q

```html
<!DOCTYPE html>
<html lang="en">
<head>
<meta charset="utf-8">
<title>Marlow &amp; Quince — Business Card</title>
<link rel="stylesheet" href="https://fonts.googleapis.com/css2?family=Cinzel:wght@500;600&family=Libre+Baskerville:wght@700&family=Arimo:wght@400&display=swap">
<style>
  :root {
    --maroon-light: #a3302f;
    --maroon: #861d1f;
    --maroon-dark: #5e0f12;
    --gold: #e7bf86;
    --gold-deep: #c9955a;
    --paper: #ffffff;
    --ink: #3a2a2a;
    --backdrop: #e9e4df;
  }
  * { margin: 0; padding: 0; box-sizing: border-box; }
  html, body { width: 1200px; height: 951px; overflow: hidden; }
  body { background: var(--backdrop); position: relative; }

  .card {
    position: absolute;
    width: 640px;
    height: 366px;
    border-radius: 22px;
    overflow: hidden;
    box-shadow: 0 14px 30px rgba(0,0,0,0.25);
  }

  /* Front */
  .card-front {
    left: 110px; top: 70px;
    background: radial-gradient(ellipse at 45% 45%, var(--maroon-light) 0%, var(--maroon) 55%, var(--maroon-dark) 100%);
  }
  .front-flourish {
    position: absolute;
    right: 20px; top: 0;
    width: 330px; height: 90px;
    border-radius: 0 0 60px 90px;
    background: linear-gradient(90deg, rgba(231,191,134,0) 0%, rgba(231,191,134,0.45) 40%, rgba(231,191,134,0.35) 100%);
  }
  .front-name {
    position: absolute;
    left: 70px; top: 128px;
    width: 330px;
    text-align: center;
    font-family: "Cinzel", serif;
    font-weight: 600;
    font-size: 34px;
    letter-spacing: 1px;
    color: var(--gold);
  }
  .front-web {
    position: absolute;
    left: 0; top: 292px;
    width: 470px;
    text-align: center;
    font-family: "Libre Baskerville", serif;
    font-weight: 700;
    font-size: 15px;
    letter-spacing: 0.5px;
    color: var(--paper);
  }

  /* Back */
  .card-back {
    left: 470px; top: 500px;
    background: var(--paper);
  }
  .back-shapes { position: absolute; inset: 0; }
  .back-name-mark {
    position: absolute;
    left: 40px; top: 52px;
    width: 260px;
    text-align: center;
    font-family: "Cinzel", serif;
    font-weight: 600;
    font-size: 27px;
    color: var(--maroon);
  }
  .contact-list {
    position: absolute;
    left: 40px; top: 208px;
    list-style: none;
    font-family: "Arimo", sans-serif;
    font-size: 17px;
    color: var(--ink);
    line-height: 22px;
  }
  .contact-list li { display: flex; align-items: center; gap: 10px; }
  .contact-list svg { width: 14px; height: 14px; flex: none; }
  .contact-list .accent { color: var(--maroon); }
  .back-title {
    position: absolute;
    right: 40px; top: 170px;
    font-family: "Libre Baskerville", serif;
    font-weight: 700;
    font-size: 22px;
    color: var(--paper);
  }
</style>
</head>
<body>

<section class="card card-front" aria-label="Business card front">
  <div class="front-flourish" role="img" aria-label="Gold floral flourish in the top corner"></div>
  <h1 class="front-name">Marlow &amp; Quince</h1>
  <p class="front-web">www.marlowquince.com</p>
</section>

<section class="card card-back" aria-label="Business card back">
  <svg class="back-shapes" viewBox="0 0 640 366" preserveAspectRatio="none" aria-hidden="true">
    <defs>
      <radialGradient id="panelShade" cx="70%" cy="50%" r="60%">
        <stop offset="0%" stop-color="#a3302f"/>
        <stop offset="100%" stop-color="#6e1416"/>
      </radialGradient>
    </defs>
    <path d="M350,366 C330,250 335,120 360,0 L372,0 C350,120 348,250 372,366 Z" fill="#e7bf86"/>
    <path d="M395,366 C365,250 370,110 420,0 L640,0 L640,366 Z" fill="url(#panelShade)"/>
    <path d="M412,0 C380,80 372,200 392,366 L384,366 C362,200 370,80 404,0 Z" fill="#861d1f"/>
  </svg>

  <h2 class="back-name-mark">Marlow &amp; Quince</h2>

  <ul class="contact-list">
    <li>
      <svg viewBox="0 0 14 14"><path d="M3 1 L5.5 1 L6.5 4 L5 5.2 C5.8 7 7 8.2 8.8 9 L10 7.5 L13 8.5 L13 11 C13 12 12 13 11 13 C5.5 13 1 8.5 1 3 C1 2 2 1 3 1 Z" fill="#5e0f12"/></svg>
      <span>555-014-2730</span>
    </li>
    <li>
      <svg viewBox="0 0 14 14"><rect x="1" y="5" width="12" height="8" rx="2" fill="#5e0f12"/><path d="M2 5 C2 1 12 1 12 5" stroke="#5e0f12" stroke-width="2" fill="none"/></svg>
      <span>555-014-2731</span>
    </li>
    <li>
      <svg viewBox="0 0 14 14"><rect x="1" y="3" width="12" height="9" rx="1" fill="#5e0f12"/><path d="M1.5 3.5 L7 8 L12.5 3.5" stroke="#fff" stroke-width="1.2" fill="none"/></svg>
      <span>hello@marlowquince.com</span>
    </li>
    <li>
      <svg viewBox="0 0 14 14"><circle cx="7" cy="7" r="6" fill="#5e0f12"/></svg>
      <span>www.<span class="accent">marlowquince</span>.com</span>
    </li>
  </ul>

  <p class="back-title">Marlow &amp; Quince</p>
</section>

</body>
</html>
```